Upscale business cards needed for Board of Directors

We need professional business cards created for members of our family business Board of Directors. We would like these relatively simple and straightforward, but also with a unique element to set them apart. Probably stick with neutral and simple colors - white, grey etc. We need space for the traditional elements, including name, title, address, email/phone number. And we will be creating several from this template so it needs to be template that is easy to switch information in and out of.
Business
See description

```html
<!DOCTYPE html>
<html lang="en">
<head>
<meta charset="utf-8">
<title>Harborline Holdings – Business Cards</title>
<link href="https://fonts.googleapis.com/css2?family=Lato:wght@400;700;900&display=swap" rel="stylesheet">
<style>
  :root {
    --gold: #b09e74;
    --ink: #111111;
    --paper: #ffffff;
    --stage: #e6e6e4;
  }
  * { margin: 0; padding: 0; box-sizing: border-box; }
  html, body {
    width: 1200px; height: 900px; overflow: hidden;
    background: var(--stage);
    font-family: "Lato", sans-serif;
  }
  .stage {
    position: relative; width: 1200px; height: 900px;
  }
  .card {
    position: absolute; left: 320px;
    width: 560px; height: 320px; overflow: hidden;
    box-shadow: 0 6px 18px rgba(0,0,0,0.18);
  }
  /* back of card */
  .card-back { top: 60px; background: var(--gold); }
  .card-back .brand {
    position: absolute; left: 0; right: 0; top: 108px;
    text-align: center; color: var(--ink);
  }
  .brand-name {
    font-family: "Lato", sans-serif; font-weight: 900;
    font-size: 44px; letter-spacing: 1px; line-height: 1;
    text-transform: uppercase;
  }
  .brand-sub {
    font-family: "Lato", sans-serif; font-weight: 900;
    font-size: 22px; letter-spacing: 12px; line-height: 1.3;
    text-transform: uppercase;
  }
  .card-back .web {
    position: absolute; left: 0; right: 0; top: 230px;
    text-align: center; color: var(--paper);
    font-size: 14px; letter-spacing: 2px;
  }
  /* front of card */
  .card-front { top: 500px; background: var(--gold); }
  .card-front .swoosh { position: absolute; inset: 0; }
  .contact {
    position: absolute; left: 28px; top: 92px;
    list-style: none; color: var(--ink); font-size: 14px; line-height: 19px;
  }
  .contact .address { margin-bottom: 4px; padding-left: 22px; }
  .contact li { display: flex; align-items: center; gap: 8px; }
  .contact svg { width: 14px; height: 14px; flex: none; fill: var(--gold); }
  .card-front .brand {
    position: absolute; left: 290px; top: 100px; color: var(--ink); text-align: center;
  }
  .card-front .brand-name { font-size: 40px; }
  .card-front .brand-sub { font-size: 20px; letter-spacing: 11px; }
  .person { position: absolute; left: 330px; top: 200px; }
  .person-name { color: var(--gold); font-size: 22px; font-weight: 400; }
  .person-title { color: var(--ink); font-size: 14px; }
</style>
</head>
<body>
<main class="stage">
  <section class="card card-back">
    <div class="brand">
      <div class="brand-name">Harborline</div>
      <div class="brand-sub">Holdings</div>
    </div>
    <div class="web">www.harborline.com</div>
  </section>

  <section class="card card-front">
    <svg class="swoosh" viewBox="0 0 560 320" preserveAspectRatio="none">
      <path d="M0 40 Q130 4 270 0 H560 V234 Q330 318 0 298 Z" fill="#ffffff"/>
      <path d="M0 46 Q135 10 285 0 H560 V228 Q330 312 0 292 Z" fill="#111111"/>
      <path d="M0 64 Q150 22 330 0 H560 V214 Q330 296 0 276 Z" fill="#ffffff"/>
    </svg>

    <ul class="contact">
      <li class="address">1450 Elm Crest<br>Lakeview TX 78100</li>
      <li><svg viewBox="0 0 24 24"><path d="M6.6 10.8a15 15 0 0 0 6.6 6.6l2.2-2.2a1 1 0 0 1 1-.25 11.4 11.4 0 0 0 3.6.57 1 1 0 0 1 1 1V20a1 1 0 0 1-1 1A17 17 0 0 1 3 4a1 1 0 0 1 1-1h3.5a1 1 0 0 1 1 1c0 1.25.2 2.45.57 3.57a1 1 0 0 1-.25 1z"/></svg>555 010 2400</li>
      <li><svg viewBox="0 0 24 24"><path d="M6 3h9l3 3v3H6zM4 10h16a2 2 0 0 1 2 2v6h-4v3H6v-3H2v-6a2 2 0 0 1 2-2zm4 6v3h8v-3z"/></svg>555 010 2401</li>
      <li><svg viewBox="0 0 24 24"><path d="M2 5h20v14H2zm2 2v.5l8 5 8-5V7l-8 5z"/></svg>info@harborline.com</li>
      <li><svg viewBox="0 0 24 24"><circle cx="12" cy="12" r="10"/></svg>www.harborline.com</li>
    </ul>

    <div class="brand">
      <div class="brand-name">Harborline</div>
      <div class="brand-sub">Holdings</div>
    </div>

    <div class="person">
      <div class="person-name">Daniel Whitford</div>
      <div class="person-title">Director</div>
    </div>
  </section>
</main>
</body>
</html>
```